Business Card for a Dental Office

The design should communicate integrity, quality and reliability. We also want the card look elegant, simple, but still stand out, different from the traditional-dental-office business card.

Industry/Entity Type

Business

```html
<!DOCTYPE html>
<html lang="en">
<head>
<meta charset="utf-8">
<title>Halden Dental Studio – Business Card</title>
<link href="https://fonts.googleapis.com/css2?family=Arimo:wght@400;700&display=swap" rel="stylesheet">
<style>
  :root {
    --backdrop: #3a3a3c;
    --gold-light: #f4e23a;
    --gold: #d8bd1c;
    --gold-deep: #8c7a10;
    --ink: #111111;
    --paper: #ffffff;
    --night: #0b0b0b;
    --white-text: #f2f2f2;
  }
  * { margin: 0; padding: 0; box-sizing: border-box; }
  html, body { width: 1200px; height: 950px; overflow: hidden; }
  body {
    background: var(--backdrop);
    font-family: "Arimo", Arial, sans-serif;
    position: relative;
  }
  .card {
    position: absolute;
    width: 560px;
    height: 320px;
    box-shadow: 0 18px 40px rgba(0,0,0,.45);
    overflow: hidden;
  }
  /* Front side */
  .card-front {
    left: 90px; top: 110px;
    background: radial-gradient(ellipse at 50% 40%, var(--gold-light) 0%, var(--gold) 45%, var(--gold-deep) 100%);
  }
  .brand {
    display: flex;
    align-items: center;
    gap: 10px;
    font-weight: 700;
    color: var(--ink);
    text-transform: uppercase;
    letter-spacing: .5px;
  }
  .brand-mark {
    width: 34px; height: 34px;
    background: var(--ink);
  }
  .card-front .brand {
    position: absolute;
    left: 50%; top: 132px;
    transform: translateX(-50%);
    font-size: 26px;
    white-space: nowrap;
  }
  .front-web {
    position: absolute;
    left: 0; right: 0; top: 222px;
    text-align: center;
    font-size: 13px;
    letter-spacing: 2px;
    color: #2a2508;
  }
  /* Back side */
  .card-back { left: 550px; top: 500px; background: var(--paper); }
  .card-back .bg { position: absolute; inset: 0; }
  .card-back .brand {
    position: absolute;
    left: 30px; top: 166px;
    font-size: 15px;
    gap: 8px;
    white-space: nowrap;
  }
  .card-back .brand-mark { width: 24px; height: 24px; }
  .person {
    position: absolute;
    right: 28px; top: 28px;
    text-align: right;
    text-transform: uppercase;
  }
  .person-name { color: var(--gold); font-size: 18px; font-weight: 700; letter-spacing: .5px; }
  .person-title { color: var(--white-text); font-size: 13px; margin-top: 4px; }
  .contact {
    position: absolute;
    right: 28px; top: 128px;
    list-style: none;
    text-align: right;
    color: var(--white-text);
    font-size: 13px;
    line-height: 21px;
  }
  .contact li { display: flex; justify-content: flex-end; align-items: center; gap: 8px; }
  .contact .icon { width: 13px; height: 13px; flex: none; }
  .contact .no-icon { padding-right: 21px; }
</style>
</head>
<body>

<section class="card card-front" aria-label="Card front">
  <div class="brand"><span class="brand-mark"></span>Halden Dental Studio</div>
  <p class="front-web">www.haldendental.com</p>
</section>

<section class="card card-back" aria-label="Card back">
  <svg class="bg" viewBox="0 0 560 320" width="560" height="320" aria-hidden="true">
    <defs>
      <linearGradient id="gold-band" x1="0" y1="0" x2="0" y2="1">
        <stop offset="0" stop-color="#f4e23a"/>
        <stop offset=".5" stop-color="#d8bd1c"/>
        <stop offset="1" stop-color="#9c8612"/>
      </linearGradient>
    </defs>
    <path d="M200,0 C330,70 320,240 235,320 L268,320 C350,240 360,80 245,0 Z" fill="url(#gold-band)"/>
    <path d="M250,0 C365,80 355,240 272,320 L560,320 L560,0 Z" fill="#0b0b0b"/>
  </svg>

  <div class="brand"><span class="brand-mark"></span>Halden Dental Studio</div>

  <div class="person">
    <p class="person-name">Mara Ellison</p>
    <p class="person-title">President</p>
  </div>

  <ul class="contact">
    <li class="no-icon">2170 Alder Crest Road</li>
    <li>Linden Bay, NY 10990
      <svg class="icon" viewBox="0 0 16 16" aria-hidden="true"><path d="M3 1h3l1.5 4-2 1.2a9 9 0 0 0 4.3 4.3L11 8.5l4 1.5v3a2 2 0 0 1-2 2A12 12 0 0 1 1 3a2 2 0 0 1 2-2z" fill="#d8bd1c"/></svg></li>
    <li>555 0142 2253
      <svg class="icon" viewBox="0 0 16 16" aria-hidden="true"><rect x="4" y="0.5" width="8" height="15" rx="1.5" fill="#d8bd1c"/><rect x="5.5" y="2.5" width="5" height="9" fill="#0b0b0b"/></svg></li>
    <li>555 0187 5335
      <svg class="icon" viewBox="0 0 16 16" aria-hidden="true"><rect x="4" y="1" width="8" height="5" fill="#d8bd1c"/><rect x="1" y="6" width="14" height="6" rx="1" fill="#d8bd1c"/><rect x="4" y="10" width="8" height="5" fill="#d8bd1c" stroke="#0b0b0b"/></svg></li>
    <li>555 0163 3856
      <svg class="icon" viewBox="0 0 16 16" aria-hidden="true"><rect x="1" y="3" width="14" height="10" rx="1" fill="#d8bd1c"/><path d="M1.5 3.5 8 9l6.5-5.5" fill="none" stroke="#0b0b0b" stroke-width="1.2"/></svg></li>
    <li>mara@haldendental.com
      <svg class="icon" viewBox="0 0 16 16" aria-hidden="true"><circle cx="8" cy="8" r="7" fill="#d8bd1c"/><circle cx="8" cy="8" r="2.5" fill="#0b0b0b"/></svg></li>
    <li class="no-icon">www.haldendental.com</li>
  </ul>
</section>

</body>
</html>
```